Residential & commercial landscaping company

Updated business cards for commercial and landscaping company. We would like to keep out logo, but just need a more updated business card.

```html
<!DOCTYPE html>
<html lang="en">
<head>
<meta charset="utf-8">
<title>Greenhollow Business Card</title>
<link rel="stylesheet" href="https://fonts.googleapis.com/css2?family=Arimo:wght@400;700&family=Tinos:wght@700&display=swap">
<style>
  :root {
    --backdrop: #2a2a2a;
    --card-white: #ffffff;
    --ink: #111111;
    --ink-soft: #444444;
    --rule: #777777;
    --leaf: #2ec43a;
    --leaf-dark: #0f9a36;
    --green-top: #4cc94a;
    --green-mid: #0b9e36;
    --green-deep: #087a2e;
  }
  * { box-sizing: border-box; margin: 0; padding: 0; }
  html, body { width: 1200px; height: 1108px; overflow: hidden; }
  body {
    background: var(--backdrop);
    display: flex;
    align-items: center;
    justify-content: center;
    gap: 80px;
    font-family: "Arimo", Arial, sans-serif;
  }
  .card {
    width: 420px;
    height: 735px;
    position: relative;
    box-shadow: 0 18px 40px rgba(0,0,0,0.55);
  }
  .card--front {
    background: var(--card-white);
    display: flex;
    flex-direction: column;
    align-items: center;
  }
  .brand-mark {
    margin-top: 190px;
    display: flex;
    align-items: center;
    gap: 14px;
  }
  .brand-mark__dot {
    width: 34px; height: 34px;
    border-radius: 50%;
    background: var(--leaf-dark);
  }
  .brand-mark__name {
    font-family: "Arimo", Arial, sans-serif;
    font-weight: 700;
    font-size: 50px;
    color: var(--ink);
    letter-spacing: -1px;
  }
  .contact {
    margin-top: 190px;
    text-align: center;
  }
  .contact__name {
    font-family: "Tinos", "Times New Roman", serif;
    font-weight: 700;
    font-size: 31px;
    color: var(--leaf);
  }
  .contact__title {
    font-size: 19px;
    color: var(--ink-soft);
    margin-top: 2px;
  }
  .contact__rule {
    width: 190px;
    height: 1px;
    background: var(--rule);
    margin: 12px auto 12px;
  }
  .contact__line {
    font-size: 19px;
    color: var(--ink);
    line-height: 1.35;
  }
  .contact__label {
    color: var(--leaf-dark);
    font-weight: 700;
  }
  .card--back {
    background: linear-gradient(180deg, var(--green-top) 0%, var(--green-mid) 55%, var(--green-deep) 100%);
  }
  .back-texture {
    position: absolute;
    inset: 0;
    background: linear-gradient(160deg, rgba(255,255,255,0.06), rgba(0,0,0,0.08));
  }
  .back-name {
    position: absolute;
    left: 0; right: 0;
    top: 470px;
    text-align: center;
    font-weight: 700;
    font-size: 44px;
    color: #ffffff;
    letter-spacing: -0.5px;
  }
</style>
</head>
<body>
  <section class="card card--front">
    <div class="brand-mark">
      <span class="brand-mark__dot"></span>
      <span class="brand-mark__name">Greenhollow</span>
    </div>
    <div class="contact">
      <p class="contact__name">Daniel Harlow Jr.</p>
      <p class="contact__title">Project Manager</p>
      <div class="contact__rule"></div>
      <p class="contact__line"><span class="contact__label">P:</span> 555-214-0371 ext.402</p>
      <p class="contact__line"><span class="contact__label">F:</span> 555-780-6619</p>
      <p class="contact__line">dan@GreenhollowLandscapes.com</p>
    </div>
  </section>
  <section class="card card--back">
    <div class="back-texture" role="img" aria-label="Faint repeated brand pattern on green"></div>
    <p class="back-name">Greenhollow</p>
  </section>
</body>
</html>
```